Calder Aviation website

We are an aviation company based in Miramar, FL but with worldwide coverage. We are involved in commercial aircraft (mostly freighters) trading, sale & leasing. Specifically, we specialized in freighters of the Veltram family (V316, V328, V335, V342, V359). We also assist with financing, sale/leaseback. Handle special aviation projects and provide consultancy services. Currently engaged in a Veltram 359 passenger to Freighter conversion (P2F).

Website Preliminary Initial Content/Sections as follows:

About Us
Founded in 2011, Calder Aviation's management has many years of experience in Aviation, a strong background in scheduled airlines with emphasis in all cargo operations, freight forwarding supply chain and freight logistics, as well as ACMI and CMI operations.

Calder’s focuses in facilitating wet and dry lease operations, charter and ACMI programs consultancy, aircraft sales, leasing and procurement, aviation consultancy and aircraft management.

Calder team is a hands-on reliable alternative that works toward achieving your aircraft and aviation objectives by meeting your requirements and timeframe throughout professional and personalized service.

Tiberio Salcedo has over three decades of experience in the aviation field including aircraft maintenance, airline management, supply chain and logistics management. Tiberio is a true entrepreneur with proven experience and expertise on the multiple facets of the commercial aviation industry throughout the creation and development of a cluster of aviation entities. Tiberio is the founder and former sole member/chairman of 64 Air, a Veltram 342 All-Cargo U.S. Certificated Air Carrier created from scratch in 2014 which nowadays conforms a superb growing airline platform with an immaculate compliance operational record.

Services

Aircraft Finance, Trading, Procurement and Leasing
Calder buys, sells, leases and facilitates aircraft trading while specializes in structured aircraft investment projects. Calder has deep industry relationships and years of expertise, allowing to successfully execute lease transactions. We assist airlines, financial institutions and leasing companies when selling or purchasing aircraft.

Aircraft Available for Sale/Lease

Sale/Leaseback
Sale-leaseback is a method of financing. If your company needs liquidity, your aircraft or engine can serve as collateral for a loan throughout a sale-leaseback transaction. Sale-leaseback can free the equity tied up in aircraft or asset. Even if there is no pressing need for funds, a sale-leaseback allows you to use the equity tied up in your aircraft in a more productive fashion. Leaseback arrangements are usually employed because they confer financing, accounting or taxation benefits.

Passenger to Freighter Conversion (P2F)
Pandemic has seen the resurgence of operators packing freight into the main cabins of passenger aircraft. Carriers have been allowed to transport cargo in the cabin by removing passenger seats completely. NAB/CARO have established exemptions that allow operators to fly in “Preighter” configuration for a limited time. Calder is closely working with a U.S. group that is developing a Class E Supplemental Type Certificate (STC) for applicability on V359 aircraft which will include a cargo door for containerized freight. Final approvals are expected during first quarter of 2022.
Wet lease
Throughout our deep relationships within the industry, Calder facilitates short or long-term wet leases to airlines and qualified parties around the globe, whereby we provide the Aircraft, Crews, Maintenance and Insurance (ACMI) worldwide services at competitive rates. We also specialize in AM leases where the aircraft is registered onto Lessee´s AOC with all maintenance services included in the rates, covering all maintenance risks, or CM or CMI where the client provides the aircraft.

Dry Lease
We offer aircraft from our own portfolio on dry lease or could engage in procuring the aircraft of your choice.

Asset & Aircraft Management
We provide aircraft owners Aircraft Management services, where we manage the technical side of the aircraft or the asset. Calder also provides Harlow Dynamics engines trading, repair and full management services. We also buy Veltram/Skylane surplus inventory.

Worldwide Charters
We facilitate the arrangement of full charters to airlines and logistics companies. Certain territory restrictions may apply.

Aviation Consultancy
We provide airline consultancy services for new or special projects. Calder also specializes on All Cargo International route analysis, implementation and development. Our team provides professional guidance in obtaining worldwide both scheduled and charter authority.

Target Market(s)

Our target market are the airlines, logistics companies and commercial aviation related entities

Industry/Entity Type

Commercial Aviation

Coding

Coded - Design and coding required

Number of Pages Required

3 page

Requirements
Must have
• Illustrations of wide body freighters such V359, V342, V328

```html
<!DOCTYPE html>
<html lang="en">
<head>
<meta charset="utf-8">
<title>Calder Aviation</title>
<link href="https://fonts.googleapis.com/css2?family=Marcellus&family=Montserrat:wght@400;500;600&display=swap" rel="stylesheet">
<style>
:root{
  --navy:#111a4d;
  --steel:#b9c6cc;
  --steel-dark:#8fa0a8;
  --light:#eff1f5;
  --text:#2f3447;
  --white:#ffffff;
  --line:#d4dade;
}
*{box-sizing:border-box;margin:0;padding:0}
html,body{width:1200px;height:3878px;overflow:hidden}
body{font-family:"Montserrat",sans-serif;color:var(--text);background:var(--white);position:relative}
.section{position:absolute;left:0;width:1200px}
.abs{position:absolute}
.heading{font-family:"Marcellus",serif;color:var(--navy);font-size:33px;letter-spacing:1px;font-weight:400}
.center{text-align:center;left:0;width:1200px}
.divider{position:absolute;height:2px;width:110px;background:linear-gradient(90deg,transparent,var(--steel-dark),transparent)}
.btn{position:absolute;background:var(--steel);color:var(--navy);font-size:15px;font-weight:500;letter-spacing:.5px;display:flex;align-items:center;justify-content:center}

/* hero */
.hero{top:0;height:610px}
.hero-photo{position:absolute;left:0;top:0;width:1200px;height:560px;background:linear-gradient(180deg,#59617a 0%,#8a93a5 30%,#6e7585 55%,#4b4f58 75%,#6a6d72 100%)}
.brand{position:absolute;color:var(--white);text-align:center;font-family:"Marcellus",serif}
.brand .name{font-size:30px;letter-spacing:1px;line-height:1}
.brand .sub{font-size:13px;letter-spacing:12px;margin-top:8px}
.nav{position:absolute;top:46px;left:562px;display:flex;gap:34px;color:var(--white);font-size:13px;align-items:center}
.nav .phone{display:flex;gap:8px;align-items:center}
.hero-title{top:222px;color:var(--white);font-family:"Marcellus",serif;font-size:29px;line-height:42px;letter-spacing:.5px}
.hero-edge{position:absolute;left:0;top:480px}

/* about */
.about{top:610px;height:560px}
.quote{position:absolute;left:163px;top:153px;width:435px;height:75px;background:linear-gradient(90deg,#d6dde1,#bcc8cd);padding:16px 14px;font-size:15px;line-height:24px;color:var(--navy)}
.about p{position:absolute;left:163px;width:435px;font-size:12.5px;line-height:23px}
.photo-circle{position:absolute;border-radius:50%}

/* services */
.services{top:1170px;height:693px;background:var(--light)}
.hub{position:absolute;border-radius:50%;background:radial-gradient(circle at 50% 35%,#ffffff 0%,#dde3e7 55%,#b9c5cb 100%)}
.svc-icon{position:absolute;width:74px;height:74px;border-radius:50%;border:1.5px solid var(--navy);background:var(--white);display:flex;align-items:center;justify-content:center}
.svc-label{position:absolute;font-size:14px;line-height:24px;color:var(--text)}
.dot{position:absolute;width:6px;height:6px;border-radius:50%;background:var(--navy)}

/* stats */
.stats{top:1863px;height:377px}
.stat{position:absolute;width:300px;text-align:center}
.stat .num{font-size:31px;font-weight:500;color:var(--navy);letter-spacing:1px}
.stat .bar{width:82px;height:2px;background:var(--steel);margin:18px auto 20px}
.stat .cap{font-size:13.5px}
.vline{position:absolute;top:190px;width:1px;height:110px;background:var(--line)}

/* clients */
.clients{top:2240px;height:376px;background:var(--light)}
.client{position:absolute;top:169px;width:200px;height:118px;background:var(--white);box-shadow:0 4px 12px rgba(17,26,77,.08);display:flex;align-items:center;justify-content:center;gap:8px;font-size:26px;font-weight:500;color:#55586a}
.client .mark{width:16px;height:16px;border-radius:50%;background:#55586a}

/* inquiry */
.inquiry{top:2616px;height:524px}
.field{position:absolute;height:44px;border:1px solid #c9ced6;background:var(--white);display:flex;align-items:center;font-size:11.5px;color:#6b7080}
.field .ico{width:38px;height:100%;border-right:1px solid #c9ced6;display:flex;align-items:center;justify-content:center;margin-right:12px}
.field.msg{align-items:flex-start}
.field.msg .ico{height:28px;margin-top:8px}
.field.msg span{margin-top:15px}

/* cta */
.cta{top:3140px;height:278px;background:var(--light)}
.cta-title{top:78px;font-family:"Marcellus",serif;color:var(--navy);font-size:30px;line-height:43px;letter-spacing:.5px}

/* footer */
.footer{top:3418px;height:460px;background:var(--navy);color:var(--white)}
.footer-edge{position:absolute;left:0;top:0}
.foot-head{font-family:"Marcellus",serif;font-size:17px;letter-spacing:.5px;color:#d7dde2}
.links{list-style:none;font-size:12.5px;line-height:30px;margin-top:8px}
.contact-row{display:flex;gap:10px;font-size:12.5px;line-height:20px;margin-top:10px}
.copyright{top:405px;font-size:12.5px}
.copyright span{color:#9fb0ff}
</style>
</head>
<body>

<section class="section hero">
  <div class="hero-photo" role="img" aria-label="Widebody freighter jet parked on a wet apron under a cloudy sky, viewed head-on"></div>
  <div class="brand" style="left:163px;top:26px">
    <div class="name">CALDER</div>
    <div class="sub">AVIATION</div>
  </div>
  <nav class="nav">
    <span>HOME</span><span>ABOUT</span><span>OUR SERVICES</span><span>CONTACT</span>
    <span class="phone"><svg width="18" height="18" viewBox="0 0 24 24" fill="none" stroke="#fff" stroke-width="1.6"><path d="M5 3h4l2 5-2.5 1.5a11 11 0 0 0 6 6L16 13l5 2v4a2 2 0 0 1-2 2A16 16 0 0 1 3 5a2 2 0 0 1 2-2z"/></svg>555 014 2290</span>
  </nav>
  <h1 class="abs center hero-title" style="font-weight:400">WIDEBODY FREIGHTERS AVAILABLE<br>TURNKEY SOLUTIONS TO SATISFY GROWING DEMAND.</h1>
  <div class="btn" style="left:530px;top:318px;width:143px;height:40px">CONTACT US</div>
  <svg class="hero-edge" width="1200" height="130" viewBox="0 0 1200 130">
    <path d="M0,50 C300,70 500,80 600,130 C700,80 900,70 1200,50 L1200,130 L0,130Z" fill="#fff"/>
    <path d="M0,20 C300,50 500,60 600,112 C700,60 900,50 1200,20 L1200,50 C900,70 700,80 600,130 C500,80 300,70 0,50Z" fill="#bcc8cc"/>
  </svg>
</section>

<section class="section about">
  <h2 class="abs heading" style="left:163px;top:78px">ABOUT US</h2>
  <div class="divider" style="left:163px;top:126px"></div>
  <div class="quote">Skylane / Veltram aircraft family expertise with over 10 years of successful business experience.</div>
  <p style="top:245px">Founded in 2011, Calder Aviation's management has many years of experience in Aviation, a strong background in scheduled airlines with emphasis in all cargo operations, freight forwarding supply chain and freight logistics, as well as ACMI and CMI operations.</p>
  <p style="top:343px">Calder’s focuses in facilitating wet and dry lease operations, charter and ACMI programs consultancy, aircraft sales, leasing and procurement, aviation consultancy and aircraft management.</p>
  <div class="btn" style="left:163px;top:432px;width:142px;height:40px">READ MORE</div>
  <div class="photo-circle" style="left:671px;top:87px;width:366px;height:366px;border:2px solid var(--steel-dark);padding:6px;background:#fff">
    <div class="photo-circle" role="img" aria-label="Business team greeting each other in front of a world map with flight routes" style="position:relative;width:100%;height:100%;background:radial-gradient(circle at 50% 40%,#6d7588,#3d4457 70%,#2c3243)"></div>
  </div>
  <div class="photo-circle" style="left:630px;top:306px;width:150px;height:150px;background:radial-gradient(circle at 50% 35%,#f2f4f6,#bdc8ce);border:5px solid #fff;display:flex;flex-direction:column;align-items:center;justify-content:center;font-family:'Marcellus',serif;color:var(--navy)">
    <div style="font-size:20px">CALDER</div>
    <div style="font-size:8px;letter-spacing:6px;margin-top:4px">AVIATION</div>
  </div>
</section>

<section class="section services">
  <h2 class="abs heading center" style="top:83px">SERVICES WE PROVIDE</h2>
  <div class="divider" style="left:545px;top:133px"></div>
  <div class="photo-circle" style="left:398px;top:199px;width:400px;height:400px;border:1px solid #dfe3e8"></div>
  <div class="hub" style="left:425px;top:226px;width:346px;height:346px"></div>
  <div class="abs" style="left:425px;top:325px;width:346px;text-align:center;font-family:'Marcellus',serif;color:var(--navy)">
    <div style="font-size:36px;letter-spacing:1px">CALDER</div>
    <div style="font-size:14px;letter-spacing:14px;margin-top:8px">AVIATION</div>
  </div>
  <div class="abs" style="left:521px;top:427px;width:150px;height:40px;border:1.5px solid var(--steel-dark);display:flex;align-items:center;justify-content:center;font-size:14px;color:var(--navy)">CONTACT US</div>

  <div class="dot" style="left:451px;top:256px"></div><div class="dot" style="left:400px;top:344px"></div>
  <div class="dot" style="left:399px;top:437px"></div><div class="dot" style="left:445px;top:526px"></div>
  <div class="dot" style="left:736px;top:256px"></div><div class="dot" style="left:787px;top:344px"></div>
  <div class="dot" style="left:789px;top:437px"></div><div class="dot" style="left:743px;top:526px"></div>

  <div class="svc-icon" style="left:376px;top:180px"><svg width="38" height="38" viewBox="0 0 24 24" fill="none" stroke="#111a4d" stroke-width="1.2"><rect x="3" y="3" width="11" height="15"/><path d="M5 7h7M5 10h7M5 13h5M12 18l9-5-2-1-4 2-3-3-1 1 2 3"/></svg></div>
  <div class="svc-label" style="left:200px;top:205px;width:166px;text-align:right">Dry Lease</div>
  <div class="svc-icon" style="left:309px;top:296px"><svg width="38" height="38" viewBox="0 0 24 24" fill="none" stroke="#111a4d" stroke-width="1.2"><circle cx="12" cy="12" r="4"/><path d="M12 2v4M12 18v4M2 12h4M18 12h4M5 5l3 3M16 16l3 3M5 19l3-3M16 8l3-3"/></svg></div>
  <div class="svc-label" style="left:120px;top:298px;width:180px;text-align:right">Asset &amp; Aircraft<br>Management</div>
  <div class="svc-icon" style="left:309px;top:412px"><svg width="38" height="38" viewBox="0 0 24 24" fill="none" stroke="#111a4d" stroke-width="1.2"><circle cx="12" cy="12" r="8"/><path d="M4 12h16M12 4c3 3 3 13 0 16M12 4c-3 3-3 13 0 16"/></svg></div>
  <div class="svc-label" style="left:110px;top:437px;width:190px;text-align:right">Worldwide Charters</div>
  <div class="svc-icon" style="left:376px;top:529px"><svg width="38" height="38" viewBox="0 0 24 24" fill="none" stroke="#111a4d" stroke-width="1.2"><circle cx="12" cy="5" r="2"/><path d="M12 7v14M8 10h8M5 14c0 4 4 7 7 7s7-3 7-7"/></svg></div>
  <div class="svc-label" style="left:170px;top:554px;width:196px;text-align:right">Aviation Consultancy</div>

  <div class="svc-icon" style="left:742px;top:180px"><svg width="38" height="38" viewBox="0 0 24 24" fill="none" stroke="#111a4d" stroke-width="1.2"><path d="M2 14l4-1 9-5 5 0-2 3-9 5-5 1z"/><circle cx="7" cy="17" r="3"/><path d="M6 17h2"/></svg></div>
  <div class="svc-label" style="left:830px;top:193px;width:220px">Aircraft Finance, Trading,<br>Procurement and Leasing</div>
  <div class="svc-icon" style="left:808px;top:296px;border-color:#d3d8dd;background:#dfe3e7"><svg width="38" height="38" viewBox="0 0 24 24" fill="none" stroke="#111a4d" stroke-width="1.2"><rect x="8" y="3" width="10" height="16"/><path d="M10 7h6M10 10h6M10 13h4M4 10v8M2 14h4"/></svg></div>
  <div class="svc-label" style="left:893px;top:321px;width:200px">Sale/Leaseback</div>
  <div class="svc-icon" style="left:808px;top:412px"><svg width="38" height="38" viewBox="0 0 24 24" fill="none" stroke="#111a4d" stroke-width="1.2"><path d="M3 8l5-1 9-3 4 1-2 2-9 3-5 1z"/><rect x="5" y="15" width="8" height="5"/><path d="M15 18h6"/></svg></div>
  <div class="svc-label" style="left:893px;top:425px;width:200px">Passenger to Freighter<br>Conversion (P2F)</div>
  <div class="svc-icon" style="left:742px;top:529px"><svg width="38" height="38" viewBox="0 0 24 24" fill="none" stroke="#111a4d" stroke-width="1.2"><path d="M4 6h8l4 3M20 18h-8l-4-3"/><rect x="9" y="8" width="6" height="8" rx="1"/></svg></div>
  <div class="svc-label" style="left:830px;top:554px;width:200px">Wet lease</div>
</section>

<section class="section stats">
  <h2 class="abs heading center" style="top:71px;line-height:40px;font-size:32px">LOREM IPSUM DOLOR SIT AMET<br>NSECTETUER ADIPISCING</h2>
  <div class="divider" style="left:545px;top:167px"></div>
  <div class="stat" style="left:141px;top:195px"><div class="num">95%</div><div class="bar"></div><div class="cap">Lorem Ipsum Dolor Sit Amet</div></div>
  <div class="vline" style="left:445px"></div>
  <div class="stat" style="left:450px;top:195px"><div class="num">12</div><div class="bar"></div><div class="cap">Lorem Ipsum Dolor Sit Amet</div></div>
  <div class="vline" style="left:754px"></div>
  <div class="stat" style="left:758px;top:195px"><div class="num">$1,84,951</div><div class="bar"></div><div class="cap">Lorem Ipsum Dolor Sit Amet</div></div>
</section>

<section class="section clients">
  <h2 class="abs heading center" style="top:78px">OUR CLIENTS &amp; ASSOCIATES</h2>
  <div class="divider" style="left:545px;top:128px"></div>
  <div class="client" style="left:163px">Archwell</div>
  <div class="client" style="left:388px"><span class="mark"></span>Genova</div>
  <div class="client" style="left:613px"><span class="mark"></span>Centrix</div>
  <div class="client" style="left:838px">Nodeline</div>
</section>

<section class="section inquiry">
  <h2 class="abs heading center" style="top:75px">QUICK INQUIRY</h2>
  <div class="divider" style="left:545px;top:125px"></div>
  <div class="field" style="left:285px;top:164px;width:307px"><span class="ico"><svg width="12" height="12" viewBox="0 0 12 12" fill="#111a4d"><circle cx="6" cy="3.5" r="2.8"/><path d="M1 12c0-3 2-5 5-5s5 2 5 5z"/></svg></span><span>First Name*</span></div>
  <div class="field" style="left:608px;top:164px;width:307px"><span class="ico"><svg width="12" height="12" viewBox="0 0 12 12" fill="#111a4d"><circle cx="6" cy="3.5" r="2.8"/><path d="M1 12c0-3 2-5 5-5s5 2 5 5z"/></svg></span><span>Last Name*</span></div>
  <div class="field" style="left:285px;top:223px;width:307px"><span class="ico"><svg width="12" height="12" viewBox="0 0 24 24" fill="#111a4d"><path d="M5 2h4l2 5-3 2a12 12 0 0 0 7 7l2-3 5 2v4a2 2 0 0 1-2 2A17 17 0 0 1 3 4a2 2 0 0 1 2-2z"/></svg></span><span>Your Phone*</span></div>
  <div class="field" style="left:608px;top:223px;width:307px"><span class="ico"><svg width="13" height="10" viewBox="0 0 13 10" fill="#111a4d"><path d="M0 0h13v1.5L6.5 5.5 0 1.5zM0 3l6.5 4L13 3v7H0z"/></svg></span><span>Your Email*</span></div>
  <div class="field msg" style="left:285px;top:282px;width:630px;height:90px"><span class="ico"><svg width="14" height="12" viewBox="0 0 14 12" fill="#111a4d"><ellipse cx="5" cy="4" rx="5" ry="3.6"/><ellipse cx="9.5" cy="7.5" rx="4.5" ry="3.2"/></svg></span><span>Your Message</span></div>
  <div class="btn" style="left:518px;top:395px;width:165px;height:40px">SUBMIT NOW</div>
</section>

<section class="section cta">
  <h2 class="abs center cta-title" style="font-weight:400">We Are Involved In Commercial Aircraft Trading, Sale &amp; Leasing,<br>We Also Specialize In Freighters of The Veltram Family</h2>
  <div class="btn" style="left:518px;top:191px;width:165px;height:40px">CONTACT US</div>
</section>

<footer class="section footer">
  <svg class="footer-edge" width="1200" height="130" viewBox="0 0 1200 130">
    <path d="M0,0 H1200 V20 C900,50 700,60 600,110 C500,60 300,50 0,20Z" fill="#eff1f5"/>
    <path d="M0,20 C300,50 500,60 600,112 C700,60 900,50 1200,20 L1200,38 C900,65 700,78 600,130 C500,78 300,65 0,38Z" fill="#bcc8cc"/>
  </svg>
  <div class="abs" style="left:161px;top:164px">
    <div class="foot-head">QUICK LINKS</div>
    <ul class="links"><li>• Home</li><li>• About</li><li>• Services</li><li>• Contact</li></ul>
  </div>
  <div class="brand" style="left:470px;top:204px;width:260px">
    <div class="name" style="font-size:36px">CALDER</div>
    <div class="sub" style="font-size:14px;letter-spacing:14px">AVIATION</div>
  </div>
  <div class="abs" style="left:852px;top:164px">
    <div class="foot-head">CONTACT DETAILS</div>
    <div class="contact-row" style="margin-top:14px"><svg width="12" height="14" viewBox="0 0 12 14" fill="none" stroke="#fff" stroke-width="1.1"><path d="M6 13s5-5 5-8a5 5 0 0 0-10 0c0 3 5 8 5 8z"/><circle cx="6" cy="5" r="1.8"/></svg><span>48 Harbor Lane, Suite 2<br>Miramar, FL 33025</span></div>
    <div class="contact-row"><svg width="13" height="13" viewBox="0 0 24 24" fill="none" stroke="#fff" stroke-width="1.6"><path d="M5 3h4l2 5-2.5 1.5a11 11 0 0 0 6 6L16 13l5 2v4a2 2 0 0 1-2 2A16 16 0 0 1 3 5a2 2 0 0 1 2-2z"/></svg><span>+1 555 014 2290</span></div>
    <div class="contact-row"><svg width="13" height="11" viewBox="0 0 13 11" fill="none" stroke="#fff" stroke-width="1.1"><rect x=".5" y=".5" width="12" height="10"/><path d="M.5 .5l6 5 6-5"/></svg><span>info@calderaviation.net</span></div>
  </div>
  <div class="abs center copyright">Copyright © 2022 <span>Calder</span>. All Rights Reserved.</div>
</footer>

</body>
</html>
```